OBK Farcoast Logistics Limited

We need the buissnes card to be very exclusive. As we are all young in our company. We need this to be the gate to make our clients feel deep interest for us.

We are focused in as International Trade advisors, and our products go from Oil Tanker Ships to Rubber balls for dogs.

Our Slogan is Bringing Far Places Near.
And our main marketing will be through Internet.

We were stablished in 2009 In Mexico and we also have offices in Hong Kong.
We have representatives in China and Europe.

Target Market(s)

Is every company or Individual that wants to develop an International Project or product development or Logistic service of Goods and people.
Some of our current projects are Ship Brokerage, Mine Brokerage, Real State and Product Pormotional development.

Industry/Entity Type

It Company

Requirements
Must have
• Our Logo and slogan, and make the card accoriding to the logo.
Nice to have
• Our Colors

```html
<!DOCTYPE html>
<html lang="en">
<head>
<meta charset="utf-8">
<title>OBK Farcoast Logistics Limited – Business Card</title>
<link rel="stylesheet" href="https://fonts.googleapis.com/css2?family=Open+Sans:wght@400;600;700&display=swap">
<style>
  :root {
    --bg: #e9e9ea;
    --paper: #ffffff;
    --sky: #1f7bc9;
    --navy: #2b3990;
    --leaf: #8cc63f;
    --ink: #4a4a4a;
    --rule: #c9c9c9;
  }
  * { box-sizing: border-box; margin: 0; padding: 0; }
  html, body {
    width: 1200px; height: 720px; overflow: hidden;
    background: var(--bg);
    font-family: "Open Sans", Arial, sans-serif;
  }
  .canvas { position: relative; width: 1200px; height: 720px; }
  .card {
    position: absolute; top: 206px;
    width: 540px; height: 308px;
    background: var(--paper);
    box-shadow: 0 2px 10px rgba(0,0,0,0.12);
    overflow: hidden;
  }
  .card--front { left: 40px; }
  .card--back { left: 620px; }

  .front-bands { position: absolute; inset: 0; }
  .person { position: absolute; right: 18px; top: 7px; text-align: right; color: var(--paper); }
  .person__name { font-size: 17px; font-weight: 700; line-height: 1.1; }
  .person__title { font-size: 11px; font-weight: 400; }

  .brand { position: absolute; left: 30px; top: 92px; }
  .brand__row { display: flex; align-items: center; gap: 8px; }
  .brand__dot { width: 14px; height: 14px; border-radius: 50%; background: var(--leaf); }
  .brand__name { font-size: 38px; font-weight: 700; color: var(--leaf); line-height: 1; letter-spacing: 1px; }
  .brand__slogan { margin-top: 4px; font-size: 10px; color: var(--sky); white-space: nowrap; }

  .contacts { position: absolute; left: 30px; top: 184px; list-style: none; }
  .contacts li { display: flex; align-items: center; gap: 7px; font-size: 13.5px; color: var(--ink); line-height: 23px; }
  .contacts svg { width: 12px; height: 12px; flex: none; }

  .divider { position: absolute; left: 232px; top: 176px; width: 1px; height: 56px; background: var(--rule); }
  .address { position: absolute; left: 248px; top: 178px; font-size: 13.5px; color: var(--ink); line-height: 22px; }

  .back-brand { position: absolute; left: 0; right: 0; top: 78px; display: flex; justify-content: center; align-items: center; gap: 12px; }
  .back-brand__dot { width: 22px; height: 22px; border-radius: 50%; background: var(--leaf); }
  .back-brand__name { font-size: 76px; font-weight: 700; color: var(--sky); line-height: 1; letter-spacing: 2px; }
  .slogan { position: absolute; left: 0; right: 0; top: 214px; text-align: center; font-size: 18px; font-weight: 600; color: var(--navy); }
  .web { position: absolute; left: 0; right: 0; top: 244px; text-align: center; font-size: 18px; color: var(--ink); letter-spacing: 3px; }
</style>
</head>
<body>
<main class="canvas">
  <section class="card card--front">
    <svg class="front-bands" viewBox="0 0 540 308" width="540" height="308" aria-hidden="true">
      <polygon points="240,0 540,0 540,48 350,48" fill="var(--sky)"/>
      <path d="M305,48 L540,48 L540,60 Q476,64 470,114 Z" fill="var(--navy)"/>
    </svg>
    <div class="person">
      <p class="person__name">Your Name</p>
      <p class="person__title">Title</p>
    </div>
    <div class="brand">
      <div class="brand__row"><span class="brand__dot"></span><span class="brand__name">OBK</span></div>
      <p class="brand__slogan">Bringing Far Places Near</p>
    </div>
    <ul class="contacts">
      <li><svg viewBox="0 0 12 12"><circle cx="6" cy="6" r="6" fill="var(--navy)"/><path d="M4 3 L5 3 L5.5 4.6 L4.8 5.2 Q5.6 6.6 6.8 7.2 L7.4 6.5 L9 7 L9 8 Q6 8.8 3.6 5.6 Q3.2 4 4 3Z" fill="#fff"/></svg>123-456-0789</li>
      <li><svg viewBox="0 0 12 12"><rect x="3" y="0.5" width="6" height="11" rx="1.2" fill="var(--navy)"/><rect x="4" y="2" width="4" height="6" fill="#fff"/></svg>123-456-0789</li>
      <li><svg viewBox="0 0 12 12"><circle cx="6" cy="6" r="6" fill="var(--navy)"/><rect x="3" y="4" width="6" height="4" fill="#fff"/><path d="M3 4 L6 6.3 L9 4" stroke="var(--navy)" stroke-width="0.8" fill="none"/></svg>info@farcoast.com</li>
      <li><svg viewBox="0 0 12 12"><circle cx="6" cy="6" r="6" fill="var(--navy)"/><circle cx="6" cy="6" r="3.5" fill="none" stroke="#fff" stroke-width="0.8"/><path d="M2.5 6 H9.5 M6 2.5 V9.5" stroke="#fff" stroke-width="0.8"/></svg>www.farcoast.com</li>
    </ul>
    <div class="divider"></div>
    <p class="address">Street Name, City Name<br>State Zip Code</p>
  </section>

  <section class="card card--back">
    <div class="back-brand"><span class="back-brand__dot"></span><span class="back-brand__name">OBK</span></div>
    <p class="slogan">Bringing Far Places Near</p>
    <p class="web">www.farcoast.com</p>
  </section>
</main>
</body>
</html>
```